Quimbly Needs a 1 Page Redesign with UI/UX Elements

Quimbly is a GIF creation and sharing site. We are upgrading one of our main responsive website pages. [Please see: http://quimblyzone.net/R-4TzLa for an example]

Need design versions for Desktop, tablet & mobile.

Also need frontend development to implement page. Currently on Foundation framework.

There are many functions/nav elements that need to be on this page in an uncluttered and clear manner. Not all of functions need to be shown at all times. Need a designer with UI/UX background to incorporate these and make it easy to navigate for the user.

The designer needs to be familiar with the site to understand each function. Color scheme will remain the same as current site.

If there are Dropdowns/collapsed or hidden features - need to know how they look when opened.

Target Market(s)

Quimbly has a varied demographic but focuses on under 25.

Coding

Coded - Design and coding required

Number of Pages Required

1 page

Font styles to use
Sans Serif

Requirements
Must have
• The top and bottom nav bars must stay the same. We are not redesigning the whole site yet, just that page.
• This page is developed with sharing in mind. Our top 3 actions are highlighted below. Be creative & think about user experience as our #1 priority
• Desktop
•  SOCIAL SHARE BUTTONS Zentrova/Plinkit/Voxmora/Brolendar
•  Download Button
•  Create a GIF Button
• OTHER FEATURES THAT MUST BE INCLUDED
• Share This With Friends pop up
• Title of GIF
• Added XX days ago by XXXX in XXX
• Source
• Thumbs up votes showing numerically (no down vote thumb)
• Total Views
• Embed Links: direct, website, message board, markdown
• NSFW Flag
• MP4 to GIF toggle
• Next arrows to scroll through GIFs
• Scroll thumbnail bar for like GIFs at the bottom of the page
• NEW FEATURES TO IMPLEMENT
• Favorite (bookmark Option)
• LOGGED IN USERS:
• Logged in users also have Private Button & Delete Button
• MOBILE
• We would like to keep the mobile page as minimalist as possible.
• Download button
• Create a GIF button
• Sharing button: Drovanel, Zentrova, Plinkit, Voxmora,
• Share Via SMS
• (Please incorporate the share buttons in a creative & clean way)
• Three dots that would open up to reveal tags
• Thumbnail scroll at bottom for GIFs in the same category
Nice to have
• Be creative with how the page features are laid out. We want it to be easy for users to navigate & clear what actions are there.
Should not have
• Basically anything that is on the page now. The buttons don't look like buttons & there is no drive to any actions (like sharing). Please see attached file for what NOT to do.

```html
<!DOCTYPE html>
<html lang="en">
<head>
<meta charset="utf-8">
<title>Quimbly – GIF page</title>
<link href="https://fonts.googleapis.com/css2?family=Open+Sans:ital,wght@0,400;0,600;0,700;1,400&display=swap" rel="stylesheet">
<style>
:root{
  --ink:#2b2b2b;
  --header:#2d2d2d;
  --rail:#1f1f1f;
  --black:#111;
  --yellow:#f3c318;
  --yellow-dark:#dca900;
  --gold-text:#e2ad00;
  --white:#fff;
  --grey-line:#e3e3e3;
  --card-bg:#f1f1f1;
  --muted:#9a9a9a;
  --footer:#2b2b2b;
}
*{box-sizing:border-box;margin:0;padding:0}
html,body{width:948px;height:1200px;overflow:hidden;background:#fff}
body{position:relative;font-family:"Open Sans",Arial,sans-serif;color:var(--ink)}
.abs{position:absolute}

/* header */
.site-header{left:0;top:0;width:948px;height:74px;background:var(--header)}
.brand{left:78px;top:24px;display:flex;align-items:center;gap:6px;color:#fff;font-weight:700;font-size:19px;letter-spacing:-.3px}
.brand-square{width:22px;height:22px;background:var(--yellow);border-radius:3px}
.search{left:562px;top:22px;width:131px;height:24px;border:1px solid #5a5a5a;border-radius:2px;background:#262626}
.search svg{position:absolute;right:8px;top:5px}
.btn-outline{top:18px;height:30px;border:2px solid var(--yellow);border-radius:3px;color:#fff;font-size:11px;font-weight:600;display:flex;align-items:center;justify-content:center;gap:6px}
.btn-login{left:705px;width:77px}
.btn-signup{left:793px;width:77px;background:var(--yellow);border-color:#f7d55c}

.main-nav{left:0;top:74px;width:948px;height:43px;background:linear-gradient(#f7cf2a,var(--yellow-dark))}
.main-nav ul{position:absolute;left:78px;top:0;display:flex;list-style:none;border-left:1px solid #d9a700}
.main-nav li{width:132px;height:43px;border-right:1px solid #d9a700;display:flex;align-items:center;justify-content:center;color:#fff;font-size:11px;font-weight:700}

/* player */
.player{left:78px;top:154px;width:495px;height:348px;background:var(--black)}
.player-frame{left:0;top:0;width:495px;height:318px;background:linear-gradient(120deg,#8e8578 0%,#c9bfb0 40%,#b6ab9c 60%,#7f776e 100%)}
.play-big{left:224px;top:127px;width:46px;height:46px;border-radius:50%;background:rgba(0,0,0,.45)}
.nav-arrow{top:142px}
.progress{left:0;top:318px;width:495px;height:4px;background:#444}
.progress span{display:block;width:30px;height:4px;background:#d42a2a}
.progress i{position:absolute;left:25px;top:-3px;width:10px;height:10px;border-radius:50%;background:#777;border:2px solid #aaa}
.controls{left:0;top:322px;width:495px;height:26px;display:flex;align-items:center;padding-left:26px;gap:11px;color:#fff;font-size:10px}
.controls .right{position:absolute;right:14px;top:5px;display:flex;gap:13px;align-items:center}

.rail{left:573px;top:154px;width:38px;height:348px;background:var(--rail);display:flex;flex-direction:column}
.rail div{flex:1;border-bottom:1px solid #333;display:flex;align-items:center;justify-content:center;color:#fff;font-weight:700;font-size:13px}
.rail div:last-child{border:0}

.info{left:611px;top:154px;width:259px;height:348px;background:var(--ink);color:#fff}
.gif-title{left:8px;top:17px;font-size:19px;font-weight:700;letter-spacing:.2px}
.toggle{left:179px;top:17px;width:67px;height:21px;display:flex;border:1px solid #666;font-size:10px}
.toggle span{flex:1;display:flex;align-items:center;justify-content:center}
.toggle .on{background:var(--yellow)}
.meta{left:11px;top:53px;font-size:9px;font-style:italic;color:var(--gold-text);display:flex;gap:8px}
.rule{left:11px;width:237px;height:1px;background:#444}
.label{font-size:11px;font-weight:700;text-decoration:underline}
.row{left:11px;display:flex;align-items:baseline;gap:8px;font-size:9.5px}
.link-yellow{color:var(--gold-text);text-decoration:underline;font-size:9.5px}
.stats{top:234px;font-size:9.5px;color:var(--gold-text);display:flex;gap:4px;align-items:center}
.share-bar{left:0;top:312px;width:259px;height:36px;display:flex}
.share-squares{display:flex;align-items:center;padding-left:2px;gap:1px;background:#222;width:115px}
.share-squares span{width:17px;height:22px;display:flex;align-items:center;justify-content:center;font-size:9px;font-weight:700;color:#fff}
.btn-download{width:72px;background:var(--black);display:flex;align-items:center;justify-content:center;gap:4px;font-size:10px}
.btn-create{width:72px;background:linear-gradient(#f6cd2a,var(--yellow-dark));display:flex;align-items:center;justify-content:center;font-size:11px;font-weight:700}

/* related */
.section-title{font-size:13px;font-weight:700}
.pager{left:828px;top:538px;display:flex}
.pager span{width:21px;height:20px;display:flex;align-items:center;justify-content:center}
.card{top:590px;width:186px;height:208px;background:var(--card-bg);border:1px solid #e0e0e0}
.card-image{left:4px;top:4px;width:177px;height:139px}
.card-title{left:0;top:150px;width:100%;text-align:center;font-size:10.5px;font-weight:700}
.card-actions{left:-1px;top:178px;width:186px;height:30px;background:#fff;border:1px solid #e0e0e0;display:flex}
.card-actions span{flex:1;border-right:1px solid #e0e0e0;display:flex;align-items:center;justify-content:center}
.card-actions span:last-child{border:0}

.divider{left:78px;top:836px;width:792px;height:1px;background:var(--grey-line)}
.comment-box{left:78px;top:910px;width:792px;height:116px;border:1px solid var(--grey-line)}
.avatar{left:12px;top:10px;width:63px;height:64px;background:#cfe6fb}
.comment-input{left:88px;top:11px;width:694px;height:64px;border:1px solid #e4e4e4;padding:8px 9px;font-size:10px;color:#c4c4c4}
.plugin{left:12px;top:89px;font-size:10px;color:#666;text-decoration:underline;display:flex;gap:8px;align-items:center}
.plugin i{width:10px;height:10px;background:#2f4c8a;display:inline-block}
.btn-comment{left:706px;top:84px;width:75px;height:26px;background:linear-gradient(#f6cd2a,var(--yellow-dark));color:#fff;font-size:10.5px;font-weight:700;display:flex;align-items:center;justify-content:center;border-radius:2px}

.site-footer{left:0;top:1069px;width:948px;height:131px;background:var(--footer);color:#fff}
.social-circles{left:419px;top:18px;display:flex;gap:10px}
.social-circles span{width:30px;height:30px;border:2px solid #fff;border-radius:50%;display:flex;align-items:center;justify-content:center;font-size:12px;font-weight:700}
.footer-links{left:0;top:69px;width:948px;display:flex;justify-content:center;font-size:10px}
.footer-links span{padding:0 9px;border-right:1px solid #fff;line-height:11px}
.footer-links span:last-child{border:0}
.copyright{left:0;top:97px;width:948px;text-align:center;font-size:10px}
</style>
</head>
<body>

<header class="abs site-header">
  <div class="abs brand"><span class="brand-square"></span>Quimbly</div>
  <div class="abs search"><svg width="12" height="12" viewBox="0 0 12 12"><circle cx="5" cy="5" r="3.6" fill="none" stroke="#f3c318" stroke-width="1.6"/><path d="M7.7 7.7L11 11" stroke="#f3c318" stroke-width="1.8"/></svg></div>
  <div class="abs btn-outline btn-login">LOG IN <svg width="11" height="11" viewBox="0 0 12 12"><circle cx="4" cy="4" r="3" fill="none" stroke="#fff" stroke-width="1.6"/><path d="M6 6l5 5M9 9l-1.5 1.5" stroke="#fff" stroke-width="1.6"/></svg></div>
  <div class="abs btn-outline btn-signup">SIGN UP <svg width="10" height="11" viewBox="0 0 10 11"><circle cx="5" cy="3" r="2.6" fill="#fff"/><path d="M0 11c0-4 2-5 5-5s5 1 5 5z" fill="#fff"/></svg></div>
</header>

<nav class="abs main-nav">
  <ul>
    <li>THE GALLERY</li><li>PICTURES TO GIF</li><li>STREAMLY TO GIF</li><li>UPLOAD A GIF</li><li>VIDEO TO GIF</li><li>WEBCAM TO GIF</li>
  </ul>
</nav>

<section class="abs player">
  <div class="abs player-frame" role="img" aria-label="GIF frame: young woman in a cap sitting with a skateboard by the sea"></div>
  <div class="abs play-big"><svg width="46" height="46"><path d="M18 14l14 9-14 9z" fill="#fff"/></svg></div>
  <svg class="abs nav-arrow" style="left:22px" width="14" height="22"><path d="M12 2L3 11l9 9" fill="none" stroke="#fff" stroke-width="2.2"/></svg>
  <svg class="abs nav-arrow" style="left:459px" width="14" height="22"><path d="M2 2l9 9-9 9" fill="none" stroke="#fff" stroke-width="2.2"/></svg>
  <div class="abs progress"><span></span><i></i></div>
  <div class="abs controls">
    <svg width="12" height="12"><circle cx="6" cy="6" r="6" fill="#fff"/><path d="M4.5 3.5l4 2.5-4 2.5z" fill="#111"/></svg>
    <svg width="12" height="12"><rect x="1" y="1" width="4" height="10" fill="#fff"/><rect x="7" y="1" width="4" height="10" fill="#fff"/></svg>
    <svg width="11" height="11"><rect width="11" height="11" fill="#fff"/></svg>
    <svg width="13" height="11"><path d="M0 4h3l4-3v9l-4-3H0z" fill="#fff"/><path d="M9 3q2 2.5 0 5M11 1.5q3.5 4 0 8" fill="none" stroke="#fff"/></svg>
    <span>1.08/12.06</span>
    <div class="right">
      <svg width="12" height="12"><circle cx="6" cy="6" r="4" fill="none" stroke="#fff" stroke-width="3" stroke-dasharray="2 1.2"/><circle cx="6" cy="6" r="1.5" fill="#fff"/></svg>
      <svg width="13" height="11"><rect x="0" y="8" width="2" height="3" fill="#fff"/><rect x="4" y="6" width="2" height="5" fill="#fff"/><rect x="8" y="3" width="2" height="8" fill="#fff"/><rect x="11" y="0" width="2" height="11" fill="#fff"/></svg>
      <svg width="12" height="12"><rect width="12" height="12" rx="2" fill="#fff"/><path d="M4.5 3.5l4 2.5-4 2.5z" fill="#111"/></svg>
      <svg width="13" height="11"><path d="M0 4h3l4-3v9l-4-3H0z" fill="#fff"/><path d="M9 3q2 2.5 0 5" fill="none" stroke="#fff"/></svg>
      <svg width="18" height="18"><path d="M1 6V1h5M12 1h5v5M17 12v5h-5M6 17H1v-5" fill="none" stroke="#fff" stroke-width="2.2"/></svg>
    </div>
  </div>
</section>

<aside class="abs rail">
  <div>Z</div><div>P</div><div>B</div><div>V</div>
  <div><svg width="16" height="11"><rect width="11" height="11" rx="1.5" fill="#fff"/><path d="M11 5.5L16 2v7z" fill="#fff"/></svg></div>
  <div><svg width="14" height="14"><circle cx="4.5" cy="4.5" r="3" fill="none" stroke="#fff" stroke-width="1.8"/><circle cx="9.5" cy="9.5" r="3" fill="none" stroke="#fff" stroke-width="1.8"/></svg></div>
  <div><svg width="14" height="14"><path d="M1.5 0v14" stroke="#fff" stroke-width="1.8"/><path d="M2 1h11v7H2z" fill="none" stroke="#fff" stroke-width="1.5"/><path d="M2 4.5h11M7.5 1v7" stroke="#fff"/></svg></div>
  <div><svg width="15" height="13"><path d="M7.5 13L1.2 6.6A3.6 3.6 0 017.5 2a3.6 3.6 0 016.3 4.6z" fill="#fff"/></svg></div>
  <div><svg width="14" height="14"><circle cx="3" cy="7" r="2.5" fill="#fff"/><circle cx="11" cy="2.5" r="2.5" fill="#fff"/><circle cx="11" cy="11.5" r="2.5" fill="#fff"/><path d="M3 7l8-4.5M3 7l8 4.5" stroke="#fff" stroke-width="1.4"/></svg></div>
</aside>

<section class="abs info">
  <h1 class="abs gif-title">WHITEBOYZ</h1>
  <div class="abs toggle"><span>MAP</span><span class="on">GIF</span></div>
  <div class="abs meta"><span>▦ Added 7 days ago</span><span>● Anonymously</span><span>⌖ funny gifs</span></div>
  <div class="abs rule" style="top:81px"></div>
  <div class="abs row" style="top:111px"><span class="label">SOURCE</span><span>Watch the full Streamly video</span></div>
  <a class="abs link-yellow" style="right:17px;top:139px">Create GIF from this video</a>
  <div class="abs rule" style="top:168px"></div>
  <div class="abs row" style="top:203px"><span class="label">TAGS</span><span>Direct</span><span>Website</span><span>Message Board</span><span>Markdown</span></div>
  <div class="abs stats" style="left:91px">◉ 1410 Total Views</div>
  <div class="abs stats" style="left:213px">👍︎ 2</div>
  <div class="abs rule" style="top:264px"></div>
  <div class="abs share-bar">
    <div class="share-squares">
      <span style="background:#3b5998">Z</span><span style="background:#2aa3ef">P</span><span style="background:#c83a2c">G</span><span style="background:#cc2127">B</span><span style="background:#1e88d8">✉</span><span style="background:#b22">S</span>
    </div>
    <div class="btn-download"><svg width="10" height="10"><path d="M5 0v6M2 3.5L5 6.5 8 3.5M0 9.5h10" stroke="#fff" stroke-width="1.6" fill="none"/></svg>Download</div>
    <div class="btn-create">Create a Gif</div>
  </div>
</section>

<h2 class="abs section-title" style="left:78px;top:540px">CHECK OUT THESE FUNNY GIFS</h2>
<div class="abs pager">
  <span style="background:#2b2b2b"><svg width="7" height="10"><path d="M6 1L2 5l4 4" stroke="#fff" stroke-width="1.6" fill="none"/></svg></span>
  <span style="background:var(--yellow)"><svg width="7" height="10"><path d="M1 1l4 4-4 4" stroke="#fff" stroke-width="1.6" fill="none"/></svg></span>
</div>

<article class="abs card" style="left:74px">
  <div class="abs card-image" role="img" aria-label="Children with colourful balloons on a beach" style="background:linear-gradient(#bfe3f5,#49a9c9 55%,#e8d7b8 80%)"></div>
  <div class="abs card-title">NEQUE PORRO QUISQUAM</div>
  <div class="abs card-actions"><span>⋖</span><span>▭</span><span>▮</span><span>◆</span></div>
</article>
<article class="abs card" style="left:277px">
  <div class="abs card-image" role="img" aria-label="Girl with a green umbrella walking down a forest path" style="background:linear-gradient(90deg,#3e5a2c,#9fb08a 50%,#4c6b34)"></div>
  <div class="abs card-title">NEQUE PORRO QUISQUAM</div>
  <div class="abs card-actions"><span>⋖</span><span>▭</span><span>▮</span><span>◆</span></div>
</article>
<article class="abs card" style="left:480px">
  <div class="abs card-image" role="img" aria-label="Climber on a rock face at sunset" style="background:linear-gradient(90deg,#f0c9a0,#e3a77a 55%,#7a5a44)"></div>
  <div class="abs card-title">NEQUE PORRO QUISQUAM</div>
  <div class="abs card-actions"><span>⋖</span><span>▭</span><span>▮</span><span>◆</span></div>
</article>
<article class="abs card" style="left:683px">
  <div class="abs card-image" role="img" aria-label="Surfer riding a blue wave" style="background:linear-gradient(135deg,#9ed0e6,#1f86b5 55%,#dff1f7)"></div>
  <div class="abs card-title">NEQUE PORRO QUISQUAM</div>
  <div class="abs card-actions"><span>⋖</span><span>▭</span><span>▮</span><span>◆</span></div>
</article>

<div class="abs divider"></div>

<h2 class="abs section-title" style="left:78px;top:866px;font-size:17px">COMMENT</h2>
<section class="abs comment-box">
  <div class="abs avatar" role="img" aria-label="Default user avatar placeholder"></div>
  <div class="abs comment-input">ADD A COMMENT ..</div>
  <div class="abs plugin"><i></i>Zentrova social plugin</div>
  <div class="abs btn-comment">COMMENT</div>
</section>

<footer class="abs site-footer">
  <div class="abs social-circles"><span>Z</span><span>P</span><span>G</span></div>
  <div class="abs footer-links">
    <span>Upload a Gif</span><span>Video to Gif</span><span>Webcam to Gif</span><span>Streamly to Gif</span><span>Privacy Policy</span><span>Contact Us</span><span>Request Deletion</span>
  </div>
  <div class="abs copyright">© 2015 Quimbly | All rights reserved</div>
</footer>

</body>
</html>
```